BUSINESS CARD - HALLORAN FIELD SERVICES

I would like to create a business card for my fertilizer spreading business. I would like to incorporate my existing logo and also a description of the services offered. The business card will be given to farmers so must be kept simple but effective. It will also be left in stores so much also be eye catching in order to stand out from other cards.

Target Market(s)

FARMERS

Requirements
Must have
• FRONT OF CARD = EXISTING LOGO + "CUSTOMISED SPREADING" below the logo

REAR Of CARD = SERVICES OFFERED AND CONTACT DETAILS

- Bulk fertilizer including Lime, Gypsum, Manure & Compost
- Granular fertilizer including Single Super, Urea, Gran-am, & Custom Blends
- Modern equipment - Autosteer & Variable Rate Capable
- Friendly & Reliable Service
- Contact Gus: 0417 552 308
Nice to have
• utilize same color scheme as existing logo

```html
<!DOCTYPE html>
<html lang="en">
<head>
<meta charset="utf-8">
<title>Halloran Field Services – Business Card</title>
<link href="https://fonts.googleapis.com/css2?family=Arimo:wght@400;700&family=Exo+2:wght@700&display=swap" rel="stylesheet">
<style>
  :root {
    --backdrop: #8c8c8c;
    --orange: #f7941d;
    --orange-deep: #de8419;
    --charcoal: #58595b;
    --body-text: #4d4d4f;
    --rule: #b5b5b5;
    --white: #ffffff;
    --cream: #f3ece2;
  }
  * { margin: 0; padding: 0; box-sizing: border-box; }
  html, body { width: 1200px; height: 1200px; overflow: hidden; }
  body {
    background: var(--backdrop);
    position: relative;
    font-family: "Arimo", Arial, sans-serif;
  }
  .card {
    position: absolute;
    top: 303px;
    width: 368px;
    height: 593px;
    overflow: hidden;
  }
  .card--front {
    left: 200px;
    background: linear-gradient(180deg, var(--orange) 0%, var(--orange) 55%, var(--orange-deep) 100%);
  }
  .card--back {
    left: 599px;
    width: 364px;
    background: var(--white);
  }

  /* Front */
  .front-name {
    position: absolute;
    left: 0; right: 0;
    top: 430px;
    text-align: center;
    color: var(--white);
    font-weight: 700;
    font-size: 31px;
    line-height: 1.1;
    letter-spacing: -0.5px;
  }
  .front-tagline {
    position: absolute;
    left: 0; right: 0;
    top: 530px;
    text-align: center;
    font-family: "Exo 2", sans-serif;
    font-weight: 700;
    font-size: 18px;
    letter-spacing: 2.5px;
    color: var(--cream);
  }

  /* Back */
  .brand-mark {
    position: absolute;
    left: 50%;
    top: 66px;
    width: 124px;
    height: 124px;
    margin-left: -62px;
    border-radius: 50%;
    background: var(--charcoal);
  }
  .back-name {
    position: absolute;
    left: 0; right: 0;
    top: 196px;
    text-align: center;
    color: var(--charcoal);
    font-weight: 700;
    font-size: 27px;
    line-height: 1.1;
    letter-spacing: -0.4px;
  }
  .services {
    position: absolute;
    left: 0; right: 0;
    top: 308px;
    list-style: none;
    text-align: center;
    color: var(--body-text);
    font-size: 16px;
    line-height: 20.5px;
  }
  .services li { margin-bottom: 6px; }
  .contact {
    position: absolute;
    left: 0; right: 0;
    top: 503px;
    text-align: center;
  }
  .contact-heading {
    display: flex;
    align-items: center;
    justify-content: center;
    gap: 8px;
    font-size: 24px;
    color: var(--body-text);
  }
  .contact-heading::before,
  .contact-heading::after {
    content: "";
    width: 64px;
    height: 1px;
    background: var(--rule);
  }
  .contact-line {
    margin-top: 4px;
    font-size: 24px;
    color: var(--body-text);
  }
  .contact-phone { color: var(--orange); }
</style>
</head>
<body>
  <section class="card card--front" aria-label="Card front">
    <h1 class="front-name">Halloran Field<br>Services</h1>
    <p class="front-tagline">CUSTOMISED SPREADING</p>
  </section>

  <section class="card card--back" aria-label="Card back">
    <div class="brand-mark" aria-hidden="true"></div>
    <h2 class="back-name">Halloran Field<br>Services</h2>
    <ul class="services">
      <li>Bulk fertilizer including Lime<br>Gypsum, Manure &amp; Compost</li>
      <li>Granular fertilizer including Single<br>Super, Urea, Gran-am, &amp; Custom Blends</li>
      <li>Modern equipment</li>
      <li>Autosteer &amp; Variable Rate Capable</li>
      <li>Friendly &amp; Reliable Service</li>
    </ul>
    <div class="contact">
      <p class="contact-heading">Contact</p>
      <p class="contact-line">Gus: <span class="contact-phone">0417 552 308</span></p>
    </div>
  </section>
</body>
</html>
```